Website for my photography business

I need a website for my photography business, Bram Kellet Photography. I need a website that has a landing page with a cover photo of each kind of photography I do. For example, Nature, Weddings, Portraits and Architecture. I want it so that when someone comes onto my website they have to choose which kind of photography page they want to visit. So if they click on the wedding photo it will open to a page with my wedding portfolio images and a contact me button. If they choose nature photography I want them to be redirected to an e-commerce section where they can purchase prints. Architecture and Portraits should open up to their respective portfolios with about me and contact info. I like this kind of format because I want people who come to my website for a specific type of photography to be able to be directed there easily without having to look at a mix of other kinds of photography. I will provide a few files to use as placeholders. I have already purchased the bramkelletphotography.example domain name. A Wix website would be great because I am most familiar with it but I am open to anything.

Industry/Entity Type

Photographer

Number of Pages Required

5+ page

Requirements
Must have
• Landing Page and e-commerce

```html
<!DOCTYPE html>
<html lang="en">
<head>
<meta charset="utf-8">
<title>Bram Kellet Photography</title>
<link href="https://fonts.googleapis.com/css2?family=Poppins:wght@400;500;600;700&family=Open+Sans:wght@400;600&display=swap" rel="stylesheet">
<style>
:root{
  --ink:#24384a;
  --text:#6b7178;
  --muted:#9aa0a6;
  --accent:#d9a23c;
  --line:#e3e5e8;
  --white:#ffffff;
  --dark:#141414;
  --darker:#0d0d0d;
  --paper:#f7f7f7;
}
*{box-sizing:border-box;margin:0;padding:0}
html,body{width:1200px;height:3672px;overflow:hidden;background:var(--white)}
body{font-family:"Open Sans",Arial,sans-serif;color:var(--text);font-size:13px;line-height:1.75}
h1,h2,h3,h4,.nav,.btn,.eyebrow,.brand{font-family:"Poppins",Arial,sans-serif}
.page{position:relative;width:1200px;height:3672px}

/* nav */
.site-nav{height:72px;display:flex;align-items:center;justify-content:center;gap:34px;font-size:11px;font-weight:500;letter-spacing:1px;color:var(--ink);text-transform:uppercase;border-bottom:1px solid var(--line)}
.site-nav .active{border-bottom:2px solid var(--accent);padding-bottom:4px}
.brand{display:flex;align-items:center;gap:8px;font-size:15px;font-weight:500;text-transform:none;letter-spacing:.5px;color:var(--ink);margin:0 26px}
.brand-dot{width:10px;height:10px;border-radius:50%;background:var(--accent)}

/* hero */
.hero{position:relative;height:528px;overflow:hidden}
.hero-photo{position:absolute;inset:0;background:linear-gradient(160deg,#1f3322 0%,#4a5a3a 28%,#b97a3e 45%,#d9dde2 62%,#f2f4f6 100%)}
.hero-panel{position:absolute;left:445px;top:150px;width:310px;height:200px;background:rgba(255,255,255,.82);text-align:center;padding:26px 24px}
.hero-panel .eyebrow{font-size:10px;letter-spacing:2px;color:var(--ink);text-transform:uppercase}
.hero-panel h1{font-size:27px;line-height:1.15;font-weight:700;color:var(--ink);letter-spacing:1px;margin:8px 0 8px}
.hero-panel p{font-size:11px;line-height:1.5;color:var(--ink)}
.hero-panel .btn{margin-top:12px}
.hero-slant{position:absolute;left:0;bottom:0;width:1200px;height:90px}

/* buttons */
.btn{display:inline-block;font-size:10px;font-weight:600;letter-spacing:1.5px;text-transform:uppercase;border:1px solid var(--accent);color:var(--accent);padding:6px 16px}
.btn.dark{border-color:var(--ink);color:var(--ink)}

/* story */
.story{height:380px;text-align:center;padding:10px 170px 0}
.eyebrow{font-size:11px;letter-spacing:2px;text-transform:uppercase;color:var(--muted)}
.story h2{font-size:18px;font-weight:600;letter-spacing:1px;color:var(--ink);text-transform:uppercase}
.story h2 span{color:var(--accent);border-bottom:2px solid var(--accent)}
.story h3{font-size:14px;font-weight:500;color:var(--accent);margin:20px 0 6px;text-align:left}
.story p{text-align:left;margin-bottom:14px}

/* service rows */
.service{display:flex;height:440px}
.service .photo{width:600px;height:440px}
.service .copy{width:600px;padding:108px 110px 0 70px}
.service .copy .eyebrow{font-size:11px;letter-spacing:.5px;text-transform:none;color:var(--text)}
.service h2{font-size:28px;font-weight:600;letter-spacing:2px;color:var(--ink);text-transform:uppercase;margin:4px 0 22px}
.service p{margin-bottom:26px}
.photo-ring{background:radial-gradient(circle at 40% 45%,#3a4250 0%,#7d6a58 30%,#a48c70 60%,#c8b49a 100%)}
.photo-forest{background:linear-gradient(90deg,#3c2a16 0%,#b35a1f 25%,#e3b15a 50%,#6f7f38 75%,#2e3a1c 100%)}
.photo-building{background:linear-gradient(180deg,#dfe6ec 0%,#b8c3cc 35%,#9a6a4e 55%,#6d4a3a 75%,#5a6658 100%)}
.photo-retouch{background:linear-gradient(135deg,#e6e6e6 0%,#a9a9a9 40%,#5a5a5a 70%,#cfcfcf 100%)}

/* testimonials */
.reviews{height:440px;text-align:center;padding-top:30px}
.reviews h2{font-size:20px;font-weight:600;letter-spacing:1.5px;color:var(--ink);text-transform:uppercase}
.reviews .intro{width:760px;margin:14px auto 30px}
.cards{display:flex;justify-content:center;gap:36px}
.card{width:300px}
.card-body{border:1px solid var(--line);padding:16px 22px 20px;position:relative;background:var(--white)}
.quote-mark{display:block;margin:0 auto 6px}
.client{display:flex;align-items:center;justify-content:center;gap:10px;margin-top:16px;font-family:"Poppins",Arial,sans-serif;font-size:12px;color:var(--ink);font-weight:500}
.avatar{width:34px;height:34px;border-radius:50%;background:linear-gradient(135deg,#9fc7e0,#4f86ad)}
.client small{display:block;font-size:10px;color:var(--muted);font-weight:400}
.dots{display:flex;justify-content:center;gap:6px;margin-top:26px}
.dots span{width:8px;height:8px;border-radius:50%;background:#cfd3d7}
.dots span.on{background:var(--accent)}

/* contact */
.contact{display:flex;height:360px}
.contact .photo{width:600px;height:360px;background:linear-gradient(180deg,#2d2a27 0%,#6b5d4e 35%,#b6a894 60%,#f0ece6 80%,#4a3f36 100%)}
.ask{width:600px;background:var(--dark);padding:26px 70px 0 80px;color:#bbb}
.ask h2{font-size:24px;font-weight:500;color:var(--white);margin-bottom:14px}
.field{display:flex;align-items:center;gap:16px;height:34px;border-bottom:1px solid #2d2d2d;font-size:11px;color:#9a9a9a}
.field svg{flex:none}
.field.message{height:58px;align-items:flex-start;padding-top:10px}
.ask .btn{margin:16px 0 0 330px;border-color:var(--accent);color:var(--accent)}

/* footer */
.site-footer{height:132px;text-align:center;padding-top:24px}
.footer-links{display:flex;justify-content:center;gap:22px;font-family:"Poppins",Arial,sans-serif;font-size:10px;color:var(--ink);text-transform:uppercase;letter-spacing:1px}
.social{display:flex;justify-content:center;gap:10px;margin:16px 0 14px}
.social span{width:24px;height:24px;border-radius:50%;border:1px solid var(--ink)}
.copyright{font-size:10px;color:var(--muted)}
</style>
</head>
<body>
<div class="page">

  <nav class="site-nav">
    <span class="active">Home</span>
    <span>Our Story</span>
    <span>Our Services ▾</span>
    <span class="brand"><span class="brand-dot"></span>Bram Kellet Photography</span>
    <span>Gallery</span>
    <span>News</span>
    <span>Contact Us</span>
  </nav>

  <header class="hero">
    <div class="hero-photo" role="img" aria-label="Red fox resting in snow beneath evergreen trees"></div>
    <div class="hero-panel">
      <div class="eyebrow">Creative Studio</div>
      <h1>PROFESSIONAL<br>PHOTOGRAPHY</h1>
      <p>Weddings, nature, portraits and architecture captured with care</p>
      <span class="btn dark">Read More</span>
    </div>
    <svg class="hero-slant" viewBox="0 0 1200 90" preserveAspectRatio="none" aria-hidden="true">
      <path d="M0 40 L360 70 Q600 95 840 70 L1200 30 L1200 90 L0 90 Z" fill="#ffffff"/>
    </svg>
  </header>

  <section class="story">
    <div class="eyebrow">Our Story</div>
    <h2><span>Bram Kellet</span> Photography</h2>
    <h3>Every Wedding, Nature, Portraits and Architecture.</h3>
    <p>Every session begins with a conversation about the people, places and feelings you want to keep. From quiet forest trails to busy reception halls, I work gently and patiently so each frame feels honest, warm and true to the day.</p>
    <p>Images are edited by hand, delivered in a private online gallery and available as fine art prints sized for your home.</p>
    <p>Whether you need a full wedding story, a portrait for your studio wall or clean architectural views for a new build, choose a collection below to see work made for that purpose.</p>
  </section>

  <section class="service">
    <div class="photo photo-ring" role="img" aria-label="Wedding rings resting on textured stone"></div>
    <div class="copy">
      <div class="eyebrow">Landscape / Weddings</div>
      <h2>Weddings</h2>
      <p>From the first look to the last dance, I follow your day closely and quietly. Candid moments, family groups and detailed portraits are gathered into one calm story you can return to for years.</p>
      <span class="btn">View Gallery</span>
    </div>
  </section>

  <section class="service">
    <div class="copy">
      <div class="eyebrow">Portraits / Nature</div>
      <h2>Nature</h2>
      <p>Mountain light, forest paths and wild coastlines photographed across every season. Many of these frames are offered as archival prints, sized and framed to bring a little of the outdoors into your home.</p>
      <span class="btn dark">View Gallery</span>
    </div>
    <div class="photo photo-forest" role="img" aria-label="Autumn forest path with tall trees and golden light"></div>
  </section>

  <section class="service">
    <div class="photo photo-building" role="img" aria-label="Modern brick and glass building with a car parked in front"></div>
    <div class="copy">
      <div class="eyebrow">Landscape / Architecture</div>
      <h2>Architecture</h2>
      <p>Clean lines, honest materials and careful light. I photograph homes, campuses and commercial buildings for architects, builders and agents who need sharp, balanced images that show a space as it really feels.</p>
      <span class="btn dark">View Gallery</span>
    </div>
  </section>

  <section class="service">
    <div class="copy">
      <div class="eyebrow">Landscape / Retouch</div>
      <h2>Retouch</h2>
      <p>Careful retouching brings out the best in every frame. Skin, tone and colour are refined by hand, distractions are removed and each image is finished to print standard while keeping it natural.</p>
      <span class="btn dark">View Gallery</span>
    </div>
    <div class="photo photo-retouch" role="img" aria-label="Black and white close study of the human form"></div>
  </section>

  <section class="reviews">
    <div class="eyebrow">Our Happy</div>
    <h2>What's Client Says</h2>
    <p class="intro">Kind words from couples, families and businesses who trusted me with their most important moments and places.</p>
    <div class="cards">
      <div class="card">
        <div class="card-body">
          <svg class="quote-mark" width="22" height="16" viewBox="0 0 22 16" aria-hidden="true"><path d="M0 16V9Q0 2 7 0l1 2Q4 4 4 8h4v8Zm12 0V9q0-7 7-9l1 2q-4 2-4 6h4v8Z" fill="#24384a"/></svg>
          <p>Bram made our wedding day feel relaxed. The photos are beautiful and full of small moments we had missed.</p>
        </div>
        <div class="client"><span class="avatar"></span><div>Nora L. Whitby<small>Client</small></div></div>
      </div>
      <div class="card">
        <div class="card-body">
          <svg class="quote-mark" width="22" height="16" viewBox="0 0 22 16" aria-hidden="true"><path d="M0 16V9Q0 2 7 0l1 2Q4 4 4 8h4v8Zm12 0V9q0-7 7-9l1 2q-4 2-4 6h4v8Z" fill="#24384a"/></svg>
          <p>Our new office finally looks the way it feels inside. Sharp, bright images delivered quickly and with great care.</p>
        </div>
        <div class="client"><span class="avatar"></span><div>Owen T. Harlan<small>Client</small></div></div>
      </div>
      <div class="card">
        <div class="card-body">
          <svg class="quote-mark" width="22" height="16" viewBox="0 0 22 16" aria-hidden="true"><path d="M0 16V9Q0 2 7 0l1 2Q4 4 4 8h4v8Zm12 0V9q0-7 7-9l1 2q-4 2-4 6h4v8Z" fill="#24384a"/></svg>
          <p>The forest print hangs above our fireplace and guests always ask about it. Lovely quality and friendly service.</p>
        </div>
        <div class="client"><span class="avatar"></span><div>Ivy R. Moss<small>Client</small></div></div>
      </div>
    </div>
    <div class="dots"><span class="on"></span><span></span><span></span></div>
  </section>

  <section class="contact">
    <div class="photo" role="img" aria-label="Bride and groom on an ornate stone staircase"></div>
    <form class="ask">
      <h2>Ask Your Question</h2>
      <div class="field"><svg width="12" height="12" viewBox="0 0 12 12"><circle cx="6" cy="4" r="3" fill="#9a9a9a"/><path d="M0 12q6-8 12 0Z" fill="#9a9a9a"/></svg>Name*</div>
      <div class="field"><svg width="12" height="12" viewBox="0 0 12 12"><rect x="0" y="2" width="12" height="8" fill="none" stroke="#9a9a9a"/><path d="M0 2l6 5 6-5" fill="none" stroke="#9a9a9a"/></svg>Email*</div>
      <div class="field"><svg width="12" height="12" viewBox="0 0 12 12"><path d="M1 2h10M1 6h10M1 10h6" stroke="#9a9a9a" stroke-width="1.5"/></svg>Subject*</div>
      <div class="field"><svg width="12" height="12" viewBox="0 0 12 12"><path d="M2 1l3 0 1 3-2 1q1 2 3 3l1-2 3 1 0 3q-9 0-9-9Z" fill="#9a9a9a"/></svg>Phone*</div>
      <div class="field message"><svg width="12" height="12" viewBox="0 0 12 12"><path d="M1 1h10v7H5l-3 3V8H1Z" fill="none" stroke="#9a9a9a"/></svg>Message*</div>
      <span class="btn">Submit</span>
    </form>
  </section>

  <footer class="site-footer">
    <div class="footer-links"><span>Home</span><span>Our Story</span><span>Our Services</span><span>Gallery</span><span>News</span><span>Contact</span></div>
    <div class="social"><span></span><span></span><span></span><span></span></div>
    <div class="copyright">© Copyright Bram Kellet Photography 2016. All Rights Reserved.</div>
  </footer>

</div>
</body>
</html>
```